Tolvik Commercial Cleaning is lookong for a new business card design.

A fresh new design that's professional and stylish. We need a serious upgrade to our business cards. I have included pictures of our existing ones. Our clients include professional individuals and business owners. We woupdblike something professional and upbeat. Please have fun and see what you come uo with.

Target Market(s)

Property managers, business owners, facility managers and other similar professionals

Industry/Entity Type

Janitorial

Contact Information for Business Card

Name, cell, office number, email, web address

Font styles to use
Sans Serif

Colors

Designer to choose colors to be used in the design.

Requirements
Must have
• please use the green color in our logo
Nice to have
• Bar code
Should not have
• Address

```html
<!DOCTYPE html>
<html lang="en">
<head>
<meta charset="utf-8">
<title>Tolvik Commercial Cleaning – Business Card</title>
<link rel="stylesheet" href="https://fonts.googleapis.com/css2?family=Open+Sans:wght@400;700&display=swap">
<style>
  :root {
    --backdrop: #232323;
    --brand-green: #3bb75a;
    --deep-green: #2e9447;
    --card-dark: #1f1f22;
    --ghost-grey: #38383b;
    --accent-blue: #3f78b8;
    --text-light: #f2f2f2;
  }
  * { margin: 0; padding: 0; box-sizing: border-box; }
  html, body {
    width: 1200px; height: 780px; overflow: hidden;
    background: var(--backdrop);
    font-family: "Open Sans", Arial, sans-serif;
  }
  .canvas { position: relative; width: 1200px; height: 780px; }

  .card {
    position: absolute;
    width: 540px; height: 308px;
    border-radius: 24px;
    box-shadow: 0 18px 36px rgba(0,0,0,.45);
    overflow: hidden;
  }

  /* Front */
  .card--front {
    left: 150px; top: 48px;
    background: var(--brand-green);
    display: flex; align-items: center; justify-content: center;
  }
  .front-name {
    color: var(--deep-green);
    font-weight: 700;
    font-size: 44px;
    line-height: 1.1;
    text-align: center;
    width: 380px;
  }

  /* Back */
  .card--back {
    left: 510px; top: 420px;
    background: var(--card-dark);
    border: 2px solid var(--brand-green);
  }
  .back-brand {
    position: absolute; left: 34px; top: 40px;
    width: 230px;
    color: var(--brand-green);
    font-weight: 700; font-size: 30px; line-height: 1.12;
  }
  .ghost-name {
    position: absolute; right: 26px; top: 52px;
    color: var(--ghost-grey);
    font-weight: 700; font-size: 78px; line-height: 1;
  }
  .side-bar {
    position: absolute; right: 0; top: 66px;
    width: 12px; height: 46px;
    background: var(--brand-green);
  }
  .person-name {
    position: absolute; right: 40px; top: 84px;
    font-weight: 700; font-size: 26px;
  }
  .person-name .first { color: var(--brand-green); }
  .person-name .last { color: var(--accent-blue); }

  .contact-list {
    position: absolute; left: 34px; bottom: 30px;
    list-style: none;
    color: var(--text-light);
    font-size: 15px; line-height: 1.55;
  }
  .contact-list li { display: flex; align-items: center; gap: 10px; }
  .contact-list svg { width: 15px; height: 15px; fill: var(--brand-green); flex: none; }
</style>
</head>
<body>
<div class="canvas">

  <section class="card card--front" aria-label="Card front">
    <h1 class="front-name">Tolvik Commercial Cleaning</h1>
  </section>

  <section class="card card--back" aria-label="Card back">
    <p class="back-brand">Tolvik Commercial Cleaning</p>
    <span class="ghost-name" aria-hidden="true">Tolvik</span>
    <span class="side-bar" aria-hidden="true"></span>
    <p class="person-name"><span class="first">Mara</span> <span class="last">Lindqvist</span></p>

    <ul class="contact-list">
      <li>
        <svg viewBox="0 0 24 24" aria-hidden="true"><path d="M6.6 10.8a15.1 15.1 0 0 0 6.6 6.6l2.2-2.2c.3-.3.7-.4 1-.2 1.1.4 2.3.6 3.6.6.6 0 1 .4 1 1V20c0 .6-.4 1-1 1A17 17 0 0 1 3 4c0-.6.4-1 1-1h3.5c.6 0 1 .4 1 1 0 1.3.2 2.5.6 3.6.1.3 0 .7-.2 1z"/></svg>
        (555) 014-2273
      </li>
      <li>
        <svg viewBox="0 0 24 24" aria-hidden="true"><path d="M2 5h20v14H2zm2 2v.5l8 5 8-5V7zm0 2.8V17h16V9.8l-8 5z"/></svg>
        mara@tolvikcleaning.com
      </li>
      <li>
        <svg viewBox="0 0 24 24" aria-hidden="true"><path d="M12 2a10 10 0 1 0 0 20 10 10 0 0 0 0-20zm6.9 6h-2.9a15 15 0 0 0-1.3-3.9A8 8 0 0 1 18.9 8zM12 4c.8 1.2 1.5 2.5 1.9 4h-3.8c.4-1.5 1.1-2.8 1.9-4zM4.3 14a8 8 0 0 1 0-4h3.4a16 16 0 0 0 0 4zm.8 2h2.9c.3 1.4.8 2.7 1.3 3.9A8 8 0 0 1 5.1 16zM8 8H5.1a8 8 0 0 1 4.2-3.9C8.8 5.3 8.3 6.6 8 8zm4 12c-.8-1.2-1.5-2.5-1.9-4h3.8c-.4 1.5-1.1 2.8-1.9 4zm2.3-6H9.7a14 14 0 0 1 0-4h4.6a14 14 0 0 1 0 4zm.4 5.9c.5-1.2 1-2.5 1.3-3.9h2.9a8 8 0 0 1-4.2 3.9zm1.6-5.9a16 16 0 0 0 0-4h3.4a8 8 0 0 1 0 4z"/></svg>
        www.tolvikcleaning.com
      </li>
    </ul>
  </section>

</div>
</body>
</html>
```